Medical consulting firm needs polished website

I am a physician and working on setting up a smal consulting firm in New Hampshire, USA. It is called Bright Harbor Medical Services, LLC and the website will be BrightHarborMed.com. I was puttering around at making my own website, and it just didn't come together nicely so I've decided to leave it to the pros. The focus of the business is Advanced Care Planning, ie planning for your future medical needs. So it deals with some heavy stuff like planning for if you get sick, who should make decisions for you, end of life options etc. So it can't be too flippant or cutesy, but also can't be too dour and dark. I am hoping to convey that by thinking ahead and making some plans you can lift some of the worries off of yourself and your family - and that we can help make a scary sounding path more manageable. I want it to be made with wordpress and I have actually already bought a template ( Vitarun – A Modern Multidisciplinary Medical & Health Theme ). The website needs to have general information about our services, doc profile, appointment maker, blog/url link page, and ideally web commerce application ( the template has access to woocommerce). I've posted my business card and current brochure (still tweaking them, but you get the idea). I am also partnering with lumenfold.com and so have included their logo and would want connections/info about them. I have the logos etc in different formats as needed.

Target Market(s)

middle aged to older adults

Industry/Entity Type

Medical

Coding

Coded - Design and coding required

Font styles to use
Sans Serif

Requirements
Must have
• as above.
Nice to have
• Ease of reading/access for elderly viewers. woo commerce.

```html
<!DOCTYPE html>
<html lang="en">
<head>
<meta charset="utf-8">
<title>Bright Harbor Medical Services – Appointments</title>
<link rel="stylesheet" href="https://fonts.googleapis.com/css2?family=Open+Sans:wght@400;600;700&display=swap">
<style>
  :root {
    --brand-blue: #2b8fd0;
    --brand-blue-dark: #1f78b4;
    --text-body: #555b61;
    --placeholder: #8a8f94;
    --field-border: #e3e6e9;
    --white: #ffffff;
    --band-dark: #3e3f42;
    --band-mid: #7a7c80;
    --band-light: #b5b7ba;
  }
  * { box-sizing: border-box; margin: 0; padding: 0; }
  html, body { width: 1200px; height: 1200px; overflow: hidden; background: var(--white); }
  body { font-family: "Open Sans", Arial, sans-serif; color: var(--text-body); position: relative; }

  .appointment { position: absolute; left: 0; top: 0; width: 1200px; height: 630px; }
  .section-title {
    position: absolute; left: 0; width: 1200px; text-align: center;
    font-weight: 700; font-size: 37px; letter-spacing: 0.5px; line-height: 1;
  }
  .appointment .section-title { top: 33px; color: var(--brand-blue); }
  .appointment .intro {
    position: absolute; left: 250px; width: 766px; top: 76px;
    text-align: center; font-size: 13.6px; line-height: 19.2px;
  }
  .doctor-photo {
    position: absolute; left: 198px; top: 165px; width: 368px; height: 465px;
    background: radial-gradient(ellipse at 50% 40%, #f1eeea 0%, #e4e4e6 55%, #f7f7f8 100%);
    border-radius: 160px 160px 0 0;
  }
  .appointment-form { position: absolute; left: 646px; top: 206px; width: 434px; }
  .field-row { display: flex; gap: 8px; margin-bottom: 6px; }
  .field {
    flex: 1; height: 32px; border: 1px solid var(--field-border); border-radius: 2px;
    background: var(--white); font-size: 10.5px; color: var(--placeholder);
    padding: 0 8px; display: flex; align-items: center; justify-content: space-between;
  }
  .field .select-arrow { border-left: 1px solid var(--field-border); height: 22px; padding-left: 10px; display: flex; align-items: center; }
  .field-message { height: 215px; align-items: flex-start; padding-top: 9px; margin-top: 1px; }
  .submit-btn {
    margin-top: 13px; width: 104px; height: 35px; border: none; border-radius: 3px;
    background: var(--brand-blue); border-bottom: 3px solid var(--brand-blue-dark);
    color: var(--white); font-family: inherit; font-weight: 700; font-size: 12px; letter-spacing: 0.3px;
  }

  .about-band {
    position: absolute; left: 0; top: 630px; width: 1200px; height: 375px;
    background: linear-gradient(100deg, var(--band-mid) 0%, var(--band-light) 22%, var(--band-dark) 45%, var(--band-mid) 62%, var(--band-light) 82%, var(--band-mid) 100%);
    color: var(--white);
  }
  .about-band .section-title { top: 97px; font-size: 35px; }
  .about-band .intro {
    position: absolute; left: 250px; width: 766px; top: 138px;
    text-align: center; font-size: 14px; line-height: 19.5px;
  }
  .stats { position: absolute; top: 223px; left: 0; width: 1200px; }
  .stat { position: absolute; width: 220px; text-align: center; }
  .stat-number { font-weight: 700; font-size: 58px; line-height: 60px; letter-spacing: -1px; }
  .stat-label { font-weight: 600; font-size: 20px; line-height: 26px; margin-top: 4px; }
</style>
</head>
<body>
  <section class="appointment">
    <h1 class="section-title">MAKE AN APPOINTMENT</h1>
    <p class="intro">Once you've done the paperwork, don't leave it in a box under the bed! We can help you store it safely and make sure it's easily available when it's needed. By partnering with Lumenfold we offer secure cloud-based storage of all of your critical information from car indurance to medical care - at a discounted rate to our clients. YOU control who can access what - and it's available from ANYWHERE and ANYTIME there's internet access.</p>

    <div class="doctor-photo" role="img" aria-label="Photo of a smiling female doctor in a white coat with a stethoscope, arms crossed"></div>

    <form class="appointment-form">
      <div class="field-row">
        <div class="field">First Name</div>
        <div class="field">Last Name</div>
      </div>
      <div class="field-row">
        <div class="field">Email Address</div>
        <div class="field">Phone No</div>
      </div>
      <div class="field-row">
        <div class="field">Appointment Date
          <svg width="12" height="12" viewBox="0 0 12 12" aria-hidden="true"><rect x="0.5" y="1.5" width="11" height="10" fill="none" stroke="#777"/><rect x="0.5" y="1.5" width="11" height="2.5" fill="#777"/><path d="M3 6h1.5M5.5 6H7M8 6h1.5M3 8.5h1.5M5.5 8.5H7M8 8.5h1.5" stroke="#777"/></svg>
        </div>
        <div class="field">Male
          <span class="select-arrow"><svg width="8" height="6" viewBox="0 0 8 6" aria-hidden="true"><path d="M0 0h8L4 6z" fill="#888"/></svg></span>
        </div>
      </div>
      <div class="field field-message">Message</div>
      <button class="submit-btn" type="button">SUBMIT</button>
    </form>
  </section>

  <section class="about-band" role="img" aria-label="Background photo of a hand touching a medical monitor screen with a heart rhythm line">
    <h2 class="section-title">ABOUT BRIGHT HARBOR</h2>
    <p class="intro">Lorem ipsum dolor sit amet, consectetuer adipiscing elit, sed diam nonummy nibh euismod tincidunt ut laoreet dolore magna aliquam erat volutpat.</p>
    <div class="stats">
      <div class="stat" style="left:172px"><div class="stat-number">180</div><div class="stat-label">AWARD SHOWS</div></div>
      <div class="stat" style="left:406px"><div class="stat-number">99</div><div class="stat-label">OUR STAFF</div></div>
      <div class="stat" style="left:640px"><div class="stat-number">50</div><div class="stat-label">CLINIC ROOMS</div></div>
      <div class="stat" style="left:874px"><div class="stat-number">362</div><div class="stat-label">MACHINES</div></div>
    </div>
  </section>
</body>
</html>
```